TK Stationery - Modern Contemporary

Develop modern template for Letterhead and Stationery (business card, letterhead, envelopes) using the TK Logo and Icon

Colors
0054AA
0677BA
7BADD7
CADEEF
E8F1F8
00AB8E
00BBA5
67D7C9
C6EFE9
E9F9F6
EE7325
F08F49
F5BC92
FAE3D3
FDF4ED
6B429C
8869AF
B7A5CE
E3DAEB
F3F0F8

```html
<!DOCTYPE html>
<html lang="en">
<head>
<meta charset="utf-8">
<title>tala kora – Stationery</title>
<link href="https://fonts.googleapis.com/css2?family=Poppins:wght@300;400;500&display=swap" rel="stylesheet">
<style>
  :root {
    --navy: #2a2f4a;
    --green: #1fbf72;
    --orange: #f07f2a;
    --paper: #ffffff;
    --paper-shade: #ececec;
    --text: #4a4d5c;
    --backdrop: #b3b3b3;
  }
  * { margin: 0; padding: 0; box-sizing: border-box; }
  html, body { width: 1200px; height: 806px; overflow: hidden; }
  body {
    position: relative;
    background: var(--backdrop);
    font-family: "Poppins", sans-serif;
    color: var(--text);
  }
  .sheet {
    position: absolute;
    background: linear-gradient(90deg, var(--paper) 55%, var(--paper-shade));
    overflow: hidden;
  }
  .brand-name {
    font-family: "Poppins", sans-serif;
    font-weight: 500;
    color: var(--navy);
    letter-spacing: 0.5px;
    white-space: nowrap;
  }
  .wave { position: absolute; left: 0; bottom: 0; }
  .web {
    position: absolute;
    color: #fff;
    font-size: 9px;
    letter-spacing: 1px;
    font-weight: 400;
  }

  /* Letterhead */
  .letterhead { left: 77px; top: 108px; width: 450px; height: 632px; }
  .letterhead .brand-name { position: absolute; left: 47px; top: 54px; font-size: 27px; }
  .contact {
    position: absolute; left: 301px; top: 41px;
    font-size: 8.5px; line-height: 11.5px; font-weight: 300;
  }
  .contact .gap { height: 4px; }
  .contact .row { display: flex; align-items: center; gap: 5px; }
  .contact svg { width: 8px; height: 8px; flex: none; }
  .letter { position: absolute; left: 41px; top: 180px; width: 371px; }
  .salutation { font-size: 11.5px; font-weight: 300; margin-bottom: 18px; }
  .letter p { font-size: 6px; line-height: 9.6px; font-weight: 300; margin-bottom: 9.5px; }
  .letter .closing { margin-top: 14px; }
  .letterhead .web { left: 303px; top: 610px; }
  .dot { position: absolute; border-radius: 50%; background: var(--orange); }
  .letterhead .dot { left: 368px; top: 543px; width: 16px; height: 16px; }

  /* Envelopes back */
  .envelope-back { position: absolute; background: linear-gradient(90deg, #f4f4f4, #e2e2e2); }
  .envelope-back.green-flap { left: 609px; top: 115px; width: 517px; height: 236px; }
  .envelope-back.navy-flap { left: 568px; top: 235px; width: 517px; height: 237px;
    box-shadow: -2px 3px 8px rgba(0,0,0,.18); }
  .flap { position: absolute; left: 0; top: 0; }
  .flap-name {
    position: absolute; left: 0; right: 0; text-align: center;
    font-family: "Poppins", sans-serif; font-weight: 400; font-size: 19px;
    color: #fff; letter-spacing: 0.5px;
  }
  .green-flap .flap-name { top: 23px; }
  .navy-flap .flap-name { top: 23px; }

  /* Envelope front */
  .envelope-front { left: 568px; top: 504px; width: 518px; height: 235px; }
  .envelope-front .brand-name { position: absolute; left: 38px; top: 24px; font-size: 27px; }
  .envelope-front .address { position: absolute; left: 38px; top: 64px; font-size: 8.5px; line-height: 11.5px; font-weight: 300; }
  .envelope-front .web { left: 363px; top: 200px; }
  .envelope-front .dot { left: 431px; top: 147px; width: 16px; height: 16px; }
</style>
</head>
<body>

<section class="sheet letterhead" aria-label="Letterhead">
  <div class="brand-name">tala kora</div>
  <div class="contact">
    <div>1420 Alder Crest Way</div>
    <div>Juneau, Alaska 34510</div>
    <div class="gap"></div>
    <div class="row">
      <svg viewBox="0 0 10 10"><path d="M2 1 L4 1 L4.6 3 L3.4 4 C4 5.4 4.8 6.2 6 6.6 L7 5.4 L9 6 L9 8 C9 8.6 8.5 9 8 9 C4.5 9 1 5.5 1 2 C1 1.5 1.4 1 2 1Z" fill="var(--green)"/></svg>
      <span>555-210-4471</span>
    </div>
    <div class="row">
      <svg viewBox="0 0 10 10"><rect x="2.5" y="0.8" width="5" height="8.4" rx="0.8" fill="none" stroke="var(--green)" stroke-width="1.2"/></svg>
      <span>555-318-9062</span>
    </div>
    <div class="row">
      <svg viewBox="0 0 10 10"><rect x="1" y="2.5" width="8" height="5.5" fill="var(--green)"/><path d="M1 2.5 L5 5.8 L9 2.5" fill="none" stroke="#fff" stroke-width="0.8"/></svg>
      <span>hello@talakora.com</span>
    </div>
  </div>

  <div class="letter">
    <div class="salutation">Dear Mr. Harlow,</div>
    <p>Thank you for meeting with our team last week to review the plans for the coming season. We have gathered the notes from that session and shaped them into a clear outline of goals, timelines and shared duties, so that every step can be checked early and adjusted where needed before the work begins.</p>
    <p>Our staff will visit each site in turn, confirm the supplies on hand and report any gaps within a few days. Where a delay appears we will call you at once, suggest a fix and agree the next step together, keeping costs steady and the schedule intact.</p>
    <p>We also propose a short monthly review in which both teams compare progress, note what has worked well and decide what to change. These meetings need not be long; a clear agenda and honest figures are enough to keep the project moving at a steady and healthy pace.</p>
    <p>Please read the enclosed summary at your convenience and send any questions you may have. We look forward to working with you and to a strong season ahead.</p>
    <p class="closing">Sincerely,</p>
  </div>

  <div class="dot"></div>
  <svg class="wave" width="450" height="80" viewBox="0 0 450 80">
    <path d="M0 24 C90 52 190 40 290 18 C360 4 410 2 450 26 L450 32 C410 10 360 12 290 26 C190 48 90 58 0 30 Z" fill="var(--green)"/>
    <path d="M0 34 C90 62 190 50 290 28 C360 14 410 14 450 38 L450 80 L0 80 Z" fill="var(--navy)"/>
  </svg>
  <div class="web">www.talakora.com</div>
</section>

<section class="envelope-back green-flap" aria-label="Envelope back with green flap">
  <svg class="flap" width="517" height="75" viewBox="0 0 517 75">
    <path d="M0 0 L517 0 L505 45 C500 65 490 74 470 74 L47 74 C27 74 17 65 12 45 Z" fill="var(--green)"/>
  </svg>
  <div class="flap-name">tala kora</div>
</section>

<section class="envelope-back navy-flap" aria-label="Envelope back with navy flap">
  <svg class="flap" width="517" height="76" viewBox="0 0 517 76">
    <path d="M0 0 L517 0 L505 45 C500 66 490 75 470 75 L47 75 C27 75 17 66 12 45 Z" fill="var(--navy)"/>
  </svg>
  <div class="flap-name">tala kora</div>
</section>

<section class="sheet envelope-front" aria-label="Envelope front">
  <div class="brand-name">tala kora</div>
  <div class="address">
    <div>1420 Alder Crest Way</div>
    <div>Juneau, Alaska 34510</div>
  </div>
  <div class="dot"></div>
  <svg class="wave" width="518" height="80" viewBox="0 0 518 80">
    <path d="M0 38 C100 62 210 52 320 30 C400 14 470 12 518 34 L518 40 C470 20 400 22 320 38 C210 58 100 70 0 44 Z" fill="var(--green)"/>
    <path d="M0 48 C100 72 210 62 320 40 C400 24 470 24 518 46 L518 80 L0 80 Z" fill="var(--navy)"/>
  </svg>
  <div class="web">www.talakora.com</div>
</section>

</body>
</html>
```